Foot doctor needs feet friendly business cards.

Business cards for Podiatrist. Needs to look professional and modern. Back side put an appointment card, and try to put a little basic street map somewhere on card along with all of our contact info below:

Marcus Dovan, DPM, Inc.
Diplomate, National Council of Lower Limb Medicine
Call: 1.877.Toes.482
1.555.283.9146
Fax: 1.555.671.3820
Email: info@DrDovanclinic.example
Web: www.DrDovanclinic.example
2847 W. Harbor Ln. Suite 204
Costa Mesa, CA 90000

```html
<!DOCTYPE html>
<html lang="en">
<head>
<meta charset="utf-8">
<title>Marcus Dovan, DPM – Business Cards</title>
<link href="https://fonts.googleapis.com/css2?family=Source+Sans+3:ital,wght@0,400;0,600;0,700;1,400;1,600&display=swap" rel="stylesheet">
<style>
  :root {
    --page-bg: #e9eaec;
    --card-bg: #ffffff;
    --brand-blue: #2d5b8e;
    --rule-blue: #5a7fa8;
    --ink: #1f1f1f;
    --photo-light: #fbf3ee;
    --photo-mid: #f2c9b6;
    --photo-deep: #e7a58c;
    --shadow: rgba(0, 0, 0, 0.14);
  }
  * { box-sizing: border-box; margin: 0; padding: 0; }
  html, body {
    width: 1200px; height: 864px; overflow: hidden;
    background: var(--page-bg);
    font-family: "Source Sans 3", "Myriad Pro", Arial, sans-serif;
  }
  .sheet {
    position: relative; width: 1200px; height: 864px;
  }
  .card {
    position: absolute; left: 310px; width: 580px; height: 331px;
    background: var(--card-bg);
    box-shadow: 0 6px 18px var(--shadow);
    overflow: hidden;
  }
  .card--appointment { top: 74px; }
  .card--contact { top: 459px; }

  /* Appointment side */
  .appt-title {
    position: absolute; top: 30px; left: 0; width: 100%;
    text-align: center; color: var(--brand-blue);
    font-style: italic; font-weight: 600; font-size: 21px;
  }
  .appt-field {
    position: absolute; left: 62px; width: 456px; height: 32px;
    border-bottom: 1px solid var(--rule-blue);
    color: var(--brand-blue); font-size: 17px;
    display: flex; align-items: flex-end; padding-bottom: 3px;
  }
  .appt-field--for { top: 60px; }
  .appt-field--date { top: 92px; }
  .appt-field--location { top: 124px; }
  .appt-field--blank { top: 156px; }
  .appt-field--blank2 { top: 188px; }
  .appt-field .time-label { position: absolute; left: 228px; bottom: 3px; }
  .appt-note {
    position: absolute; top: 228px; left: 0; width: 100%;
    text-align: center; color: var(--brand-blue);
    font-style: italic; font-size: 16.5px; line-height: 21px;
  }
  .appt-web {
    position: absolute; top: 280px; left: 0; width: 100%;
    text-align: center; color: var(--brand-blue); font-size: 16.5px;
  }

  /* Contact side */
  .feet-photo {
    position: absolute; right: 0; top: 60px; width: 360px; height: 271px;
    background:
      radial-gradient(ellipse 28% 48% at 42% 55%, var(--photo-mid), transparent 70%),
      radial-gradient(ellipse 28% 48% at 72% 52%, var(--photo-mid), transparent 70%),
      radial-gradient(ellipse 60% 70% at 58% 60%, var(--photo-deep), transparent 80%),
      linear-gradient(90deg, var(--card-bg) 0%, var(--photo-light) 30%, var(--photo-light) 100%);
    opacity: 0.9;
  }
  .name {
    position: absolute; top: 24px; left: 40px;
    color: var(--brand-blue); font-weight: 600; font-size: 27px;
  }
  .credential {
    position: absolute; top: 58px; left: 40px;
    color: var(--ink); font-size: 17px;
  }
  .address {
    position: absolute; top: 104px; left: 40px;
    color: var(--ink); font-size: 17px; line-height: 22px;
  }
  .contact-list {
    position: absolute; top: 168px; left: 40px; list-style: none;
    color: var(--ink); font-size: 17px; line-height: 22px;
  }
  .contact-list li { display: flex; align-items: center; height: 22px; }
  .contact-list .icon {
    width: 14px; height: 14px; margin-right: 8px; flex: none;
    fill: var(--brand-blue); stroke: var(--brand-blue);
  }
  .contact-list .indent { padding-left: 22px; }
</style>
</head>
<body>
<main class="sheet">

  <section class="card card--appointment" aria-label="Appointment card">
    <h2 class="appt-title">Appointment</h2>
    <div class="appt-field appt-field--for">For :</div>
    <div class="appt-field appt-field--date">Date :<span class="time-label">Time :</span></div>
    <div class="appt-field appt-field--location">Location :</div>
    <div class="appt-field appt-field--blank"></div>
    <p class="appt-note">If you are unable to keep appointment, please contact<br>us as soon as possible. Call 877 555 0142</p>
    <p class="appt-web">www.DrDovanclinic.example</p>
  </section>

  <section class="card card--contact" aria-label="Contact card">
    <div class="feet-photo" role="img" aria-label="Soft-focus photo of a baby's bare feet"></div>
    <h1 class="name">Marcus Dovan, DPM, Inc.</h1>
    <p class="credential">Diplomate, National Council of Lower Limb Medicine</p>
    <p class="address">2847 W. Harbor Ln. Suite 204<br>Costa Mesa, CA 90000</p>
    <ul class="contact-list">
      <li>
        <svg class="icon" viewBox="0 0 14 14" aria-hidden="true"><path stroke="none" d="M1 4c0-2 2-3 6-3s6 1 6 3v1H10V4H4v1H1zM3 6h8l1 6H2z"/></svg>
        1.877.Toes.482
      </li>
      <li class="indent">1.555.283.9146</li>
      <li>
        <svg class="icon" viewBox="0 0 14 14" aria-hidden="true"><path stroke="none" d="M4 1h6v3H4zM2 5h10v8H2zM4 7v2h6V7z" fill-rule="evenodd"/></svg>
        1.555.671.3820
      </li>
      <li>
        <svg class="icon" viewBox="0 0 14 14" aria-hidden="true"><rect x="1" y="3" width="12" height="8" stroke="none"/><path d="M1.5 3.5 7 8l5.5-4.5" fill="none" stroke="#fff" stroke-width="1.2"/></svg>
        info@DrDovanclinic.example
      </li>
      <li>
        <svg class="icon" viewBox="0 0 14 14" aria-hidden="true"><g fill="none" stroke-width="1.6"><rect x="1" y="6" width="7" height="4" rx="2" transform="rotate(-45 4.5 8)"/><rect x="6" y="4" width="7" height="4" rx="2" transform="rotate(-45 9.5 6)"/></g></svg>
        www.DrDovanclinic.example
      </li>
    </ul>
  </section>

</main>
</body>
</html>
```